quickdeedsale.com redesign with wireframes, white space and custom form are very important

Need a new two column design that will convert easily to mobile responsive. Lots of white space. Winning design will probably be based on header area and making the custom form stand out. I want the header to be very much like www.tallgatevk.com except the form not to go up into the header.
Here are some of the websites I really like:
www.birchdwell.com
http://ourplotpurchasedirect.com/
http://kellbrightproperty.com/

We buy homes for cash and close fast. Our target is a home seller who is desperate to sell quickly.
I have uploaded my really ugly wireframe and my logo. I also uploaded my photo for the about us box and a possible photo to use for the header.
The copy on the wireframe is what I will be using except for the about us box.

Here is the exact link for video to frame in the top left box.
https://clipvault.example/Qm38pzrtLa

0592cd
85cae6
eaf1f7
fbee3d
ec1f27

• Everything on wireframe.
• Must use Verdana font and nothing should be smaller than 12 point. Most should be in 14 point. (except maybe inside of form)

```html
<!DOCTYPE html>
<html lang="en">
<head>
<meta charset="utf-8">
<title>quickdeedsale.com – Sell Your Home Fast</title>
<link href="https://fonts.googleapis.com/css2?family=Open+Sans:wght@400;600;700&family=Oswald:wght@500;600&display=swap" rel="stylesheet">
<style>
:root{
  --blue:#0592cd;
  --sky:#85cae6;
  --mist:#eaf1f7;
  --yellow:#fbee3d;
  --red:#ec1f27;
  --ink:#2b2b2b;
  --muted:#666;
  --dark:#2e2e2e;
  --darker:#222;
  --line:#d9e2ea;
}
*{box-sizing:border-box;margin:0;padding:0}
html,body{width:1200px;height:2980px;overflow:hidden}
body{font-family:"Open Sans",Verdana,sans-serif;color:var(--ink);background:#fff;font-size:15px;line-height:1.5;position:relative}
a{color:inherit;text-decoration:none}

.site-header{height:112px;display:flex;align-items:center;justify-content:space-between;padding:0 90px}
.brand{display:flex;align-items:center;gap:12px}
.brand-mark{width:40px;height:40px;background:var(--red)}
.brand-name{font-size:30px;font-weight:700;color:var(--red)}
.header-contact{text-align:right}
.header-contact .note{font-size:14px;color:var(--muted)}
.header-contact .phone{font-size:30px;font-weight:700;color:var(--red);display:flex;align-items:center;gap:10px;justify-content:flex-end}

.main-nav{height:48px;background:linear-gradient(var(--blue),#0480b5);display:flex;padding:0 90px}
.main-nav a{color:#fff;font-size:14px;font-weight:600;text-transform:uppercase;padding:0 26px;line-height:48px}
.main-nav a.active{background:#04334a}

.hero{height:388px;position:relative;background:linear-gradient(180deg,#9fc3df 0%,#c8d9e6 40%,#8c8573 70%,#6f8a55 100%)}
.hero-caption{position:absolute;left:90px;bottom:40px;background:rgba(0,0,0,.7);padding:14px 22px;color:#fff;font-family:Oswald,sans-serif;font-size:30px;line-height:1.25;text-transform:uppercase}

.content{display:flex;gap:40px;padding:0 90px}
.main-col{width:660px}
.side-col{width:320px}

.benefits{padding-top:30px}
.benefits h2{font-size:22px;font-weight:600;margin-bottom:12px}
.tick-list{list-style:none}
.tick-list li{display:flex;align-items:center;gap:10px;font-size:15px;color:var(--muted);margin-bottom:6px}
.tick-list svg{flex:none}
.watch{font-weight:700;font-size:15px;margin:24px 0 12px}
.video{height:300px;background:linear-gradient(#6ea5d6,#2f5e96);position:relative}
.video-bar{height:30px;background:#1b1b1b;display:flex;align-items:center;gap:14px;padding:0 12px}
.video-bar .track{flex:1;height:4px;background:#555}
.video-bar .track span{display:block;width:18%;height:4px;background:var(--red)}

.pitch{margin-top:34px}
.pitch h2{font-size:22px;font-weight:600;line-height:1.35;margin-bottom:12px}
.pitch p{font-size:14px;color:var(--muted)}
.pitch p strong{color:var(--red)}
.reasons h3{font-size:20px;font-weight:700;color:var(--red);margin:28px 0 10px}
.reasons li{color:var(--muted);font-size:15px}
.reasons li.hl{color:var(--red)}
.help{margin-top:20px}
.help h3{font-size:20px;font-weight:600}
.help p{font-size:20px;font-weight:600}

.section-bar{background:var(--blue);color:#fff;font-size:22px;font-weight:600;padding:8px 18px;margin-top:30px}
.post{display:flex;gap:20px;padding:22px 0;border-bottom:1px solid var(--line)}
.post-meta{width:180px;flex:none}
.post-meta .date{font-size:12px;color:var(--muted);margin-bottom:6px}
.post-thumb{width:180px;height:120px;background:linear-gradient(#9cc0de,#7c8a68)}
.post-body{padding-top:24px}
.post-body p{font-size:14px;color:var(--muted);margin-bottom:10px}
.post-actions{display:flex;gap:8px}
.btn-red,.btn-dark{font-size:13px;color:#fff;padding:6px 14px}
.btn-red{background:var(--red)}
.btn-dark{background:var(--dark)}
.archive-box{background:var(--mist);padding:20px;display:flex;flex-wrap:wrap;gap:12px}
.archive-box a{background:var(--dark);color:#fff;font-size:14px;padding:8px 18px}

.lead-form{margin-top:-1px;border:1px solid var(--line)}
.lead-form .form-head{background:var(--red);color:#fff;padding:14px 18px}
.lead-form .form-head strong{font-size:18px;display:block;text-transform:uppercase}
.lead-form .form-head span{font-size:13px}
.form-body{background:var(--mist);padding:16px 18px}
.field{height:34px;background:#fff;border:1px solid #cfd8e0;margin-bottom:10px;font-size:12px;color:#999;padding:7px 10px}
.submit{background:var(--blue);color:#fff;font-size:17px;font-weight:700;text-align:center;padding:12px;text-transform:uppercase;margin-top:6px}

.privacy-row{display:flex;align-items:center;gap:14px;margin-top:22px}
.privacy-row .btn-red{font-size:14px}
.call-note{font-size:15px;font-weight:600;margin-top:16px}

.side-block{margin-top:34px}
.side-block h3{font-size:22px;font-weight:600;margin-bottom:10px}
.side-block p{font-size:14px;color:var(--muted)}
.reviewer{display:flex;align-items:center;gap:10px;margin-top:14px}
.reviewer .pic{width:44px;height:44px;border-radius:50%;background:#a6b7c6}
.reviewer strong{font-size:14px;display:block}
.reviewer span{font-size:12px;color:var(--muted)}
.about{border:1px solid var(--line);padding:16px}
.about .row{display:flex;gap:12px}
.about .pic{width:100px;height:118px;flex:none;background:linear-gradient(#b7c6d3,#55606a)}
.cities{background:var(--mist);padding:18px}
.cities h3{font-size:19px;line-height:1.3}
.city-list{display:grid;grid-template-columns:1fr 1fr;margin:10px 0;column-gap:8px}
.city-list span{font-size:13px;color:var(--ink);display:flex;align-items:center;gap:6px;line-height:1.65}
.city-list span::before{content:"";width:7px;height:7px;background:var(--blue);flex:none}
.cities .hl{font-size:13px;color:var(--red)}
.we-buy{border:1px solid var(--line);padding:16px}
.we-buy .pics{display:flex;gap:10px;margin:8px 0 10px}
.we-buy .pics div{flex:1;height:86px;background:linear-gradient(#a7c5df,#7e8a63)}

.site-footer{position:absolute;left:0;top:2660px;width:1200px;height:280px;background:var(--dark);color:#ccc;display:flex;gap:40px;padding:34px 90px}
.site-footer section{flex:1}
.site-footer h4{color:#fff;font-size:16px;text-transform:uppercase;margin-bottom:14px}
.site-footer p,.site-footer li{font-size:13px;list-style:none;line-height:1.8}
.site-footer .dot{display:inline-block;width:8px;height:8px;background:var(--sky);margin-right:8px}
.bottom-strip{position:absolute;left:0;top:2940px;width:1200px;height:40px;background:var(--darker);color:#999;font-size:12px;display:flex;justify-content:space-between;align-items:center;padding:0 90px}
</style>
</head>
<body>

<header class="site-header">
  <div class="brand"><span class="brand-mark"></span><span class="brand-name">quickdeedsale.com</span></div>
  <div class="header-contact">
    <div class="note">Nights and weekends ok</div>
    <div class="phone">
      <svg width="26" height="26" viewBox="0 0 24 24"><path fill="#ec1f27" d="M6.6 10.8c1.4 2.8 3.8 5.1 6.6 6.6l2.2-2.2c.3-.3.7-.4 1-.2 1.1.4 2.3.6 3.6.6.6 0 1 .4 1 1V20c0 .6-.4 1-1 1C10.6 21 3 13.4 3 4c0-.6.4-1 1-1h3.5c.6 0 1 .4 1 1 0 1.3.2 2.5.6 3.6.1.3 0 .7-.2 1z"/></svg>
      407-555-0148
    </div>
  </div>
</header>

<nav class="main-nav">
  <a class="active" href="#">Home</a><a href="#">Sell Your Home</a><a href="#">How It Works</a><a href="#">Stop Foreclosure</a><a href="#">Probate</a><a href="#">Contact Us</a>
</nav>

<div class="hero" role="img" aria-label="Photo of a large two-storey family home under a blue sky">
  <div class="hero-caption">Sell your home for cash in 8 days<br>We buy houses nationwide</div>
</div>

<div class="content">
  <main class="main-col">
    <section class="benefits">
      <h2>These are the benefits of selling your home to us:</h2>
      <ul class="tick-list">
        <li><svg width="16" height="16" viewBox="0 0 16 16"><path d="M2 8l4 4 8-8" stroke="#0592cd" stroke-width="2.5" fill="none"/></svg>You pick the closing date.</li>
        <li><svg width="16" height="16" viewBox="0 0 16 16"><path d="M2 8l4 4 8-8" stroke="#0592cd" stroke-width="2.5" fill="none"/></svg>Pay you NO Commissions or Fees.</li>
        <li><svg width="16" height="16" viewBox="0 0 16 16"><path d="M2 8l4 4 8-8" stroke="#0592cd" stroke-width="2.5" fill="none"/></svg>You don't have to paint, clean or make repairs</li>
      </ul>
      <p class="watch">Watch to see our president Glen explain how easy it is to sell to us:</p>
      <div class="video" role="img" aria-label="Video still of the company president speaking to camera"></div>
      <div class="video-bar">
        <svg width="14" height="14" viewBox="0 0 14 14"><path d="M2 1l11 6-11 6z" fill="#fff"/></svg>
        <div class="track"><span></span></div>
        <svg width="16" height="14" viewBox="0 0 16 14"><rect x="1" y="1" width="14" height="12" fill="none" stroke="#fff" stroke-width="2"/></svg>
      </div>
    </section>

    <section class="pitch">
      <h2>Sell your home or house fast for cash to a professional investor company. We buy Houses and close quickly.</h2>
      <p>Selling a home on your own has never been easier. From Orlando to Greensboro – and all points in between – you can sell your home today without any hassles. Call <strong>1-800-555-0148</strong> or fill out the form below to get a written offer on your home in just 36 hours. Sell today online to people that care.</p>
    </section>

    <section class="reasons">
      <h3>IF YOU NEED TO SELL A HOME FAST BECAUSE OF:</h3>
      <ul class="tick-list">
        <li><svg width="16" height="16" viewBox="0 0 16 16"><path d="M2 8l4 4 8-8" stroke="#0592cd" stroke-width="2.5" fill="none"/></svg>Divorce or Bankruptcy</li>
        <li><svg width="16" height="16" viewBox="0 0 16 16"><path d="M2 8l4 4 8-8" stroke="#0592cd" stroke-width="2.5" fill="none"/></svg>Foreclosure</li>
        <li class="hl"><svg width="16" height="16" viewBox="0 0 16 16"><path d="M2 8l4 4 8-8" stroke="#0592cd" stroke-width="2.5" fill="none"/></svg>Landlord problems - evictions with tenants okay</li>
        <li><svg width="16" height="16" viewBox="0 0 16 16"><path d="M2 8l4 4 8-8" stroke="#0592cd" stroke-width="2.5" fill="none"/></svg>Inherited property in probate</li>
        <li><svg width="16" height="16" viewBox="0 0 16 16"><path d="M2 8l4 4 8-8" stroke="#0592cd" stroke-width="2.5" fill="none"/></svg>Termites, mold, flood or fire damage, leaky roof</li>
        <li><svg width="16" height="16" viewBox="0 0 16 16"><path d="M2 8l4 4 8-8" stroke="#0592cd" stroke-width="2.5" fill="none"/></svg>Moving or can't afford your mortgage payments</li>
      </ul>
    </section>

    <section class="help">
      <h3>We Can Help.</h3>
      <p>We are the fastest home buyers around.</p>
    </section>

    <section class="blog">
      <div class="section-bar">Our Blog</div>
      <article class="post">
        <div class="post-meta"><div class="date">04-02-2015 · by admin</div><div class="post-thumb" role="img" aria-label="Photo of a suburban house"></div></div>
        <div class="post-body"><p>Quick notes on preparing a house for a cash sale, what to expect from an offer, and how closing dates are set by you the seller.</p>
          <div class="post-actions"><a class="btn-red" href="#">11 Comments</a><a class="btn-dark" href="#">Leave your Comments</a></div></div>
      </article>
      <article class="post">
        <div class="post-meta"><div class="date">04-02-2015 · by admin</div><div class="post-thumb" role="img" aria-label="Photo of a suburban house"></div></div>
        <div class="post-body"><p>How homeowners facing foreclosure can still walk away with cash, and the simple steps that keep the whole process fast and calm.</p>
          <div class="post-actions"><a class="btn-red" href="#">11 Comments</a><a class="btn-dark" href="#">Leave your Comments</a></div></div>
      </article>
      <article class="post">
        <div class="post-meta"><div class="date">04-02-2015 · by admin</div><div class="post-thumb" role="img" aria-label="Photo of a suburban house"></div></div>
        <div class="post-body"><p>Selling inherited property in probate can feel slow. Here is how a direct buyer shortens the wait and removes repair costs.</p>
          <div class="post-actions"><a class="btn-red" href="#">11 Comments</a><a class="btn-dark" href="#">Leave your Comments</a></div></div>
      </article>
    </section>

    <section class="archives">
      <div class="section-bar">Archives</div>
      <div class="archive-box">
        <a href="#">Sell My House</a><a href="#">Fast Cash for Homes</a><a href="#">We Buy Houses</a><a href="#">Real Estate Investor</a><a href="#">Latest</a>
      </div>
    </section>
  </main>

  <aside class="side-col">
    <form class="lead-form">
      <div class="form-head"><strong>Yes, I want to sell my home fast!</strong><span>Get a no obligation written offer in 36 hours</span></div>
      <div class="form-body">
        <div class="field">Your Name</div>
        <div class="field">Your Phone Number</div>
        <div class="field">Your Email Address</div>
        <div class="field">Property address including City, State &amp; Zip</div>
        <div class="field">Reason wanted to sell</div>
        <div class="field">Asking Price</div>
        <div class="submit">Submit to get started</div>
      </div>
    </form>

    <div class="privacy-row"><a class="btn-red" href="#">Our Privacy Policy</a><span style="font-size:13px;color:#666">Call 8am to 10 pm Eastern time.</span></div>
    <p class="call-note">We answer our phones.</p>

    <section class="side-block">
      <h3>Home Seller Testimonials</h3>
      <p>I just wanted to thank you for buying my home in Winter Park. You made it fast and easy and kept me well informed the whole way.</p>
      <div class="reviewer"><div class="pic" role="img" aria-label="Reviewer portrait"></div><div><strong>Dalen Marsh</strong><span>Winter Park</span></div></div>
    </section>

    <section class="side-block about">
      <h3>About Us</h3>
      <div class="row"><p>Owned and operated in Orlando Florida since 2001. Glen has bought and sold hundreds of homes and treats every seller with care.</p><div class="pic" role="img" aria-label="Portrait of the company owner"></div></div>
    </section>

    <section class="side-block cities">
      <h3>Some of the Cities where we Buy Houses. Not all are Listed.</h3>
      <p>These are the cities where we have an office where you can sell a home fast.</p>
      <div class="city-list">
        <span>Orlando</span><span>Harrisburg</span><span>Jacksonville</span><span>Virginia Beach</span><span>Ft Myers</span><span>Virginia Homes</span><span>Tampa</span><span>Greensboro</span><span>St. Pete</span><span>Charlotte SC</span><span>Gainesville</span><span>Port Charlotte</span><span>Tallahassee</span><span>Lake Florida</span><span>Melbourne</span><span>Wilmington</span><span>West Palm Beach</span><span>Columbia</span><span>Apopka</span><span>Titusville</span><span>Deland</span><span>Valdosta</span><span>Kissimmee</span><span>Houston</span><span>Camden Atlanta</span><span>Denver</span><span>San Antonio</span><span>Phoenix</span>
      </div>
      <p class="hl">If you don't see your city, we will probably buy homes there.</p>
    </section>

    <section class="side-block we-buy">
      <h3>We Buy</h3>
      <div class="pics"><div role="img" aria-label="Photo of a house"></div><div role="img" aria-label="Photo of a house"></div><div role="img" aria-label="Photo of a house"></div></div>
      <p>We buy nice pretty houses and some ugly ones as well.</p>
    </section>
  </aside>
</div>

<footer class="site-footer">
  <section><h4>Why Us</h4><p>We pay cash, close on your schedule and handle every repair so you can move on without stress or surprise costs.</p></section>
  <section><h4>Site Links</h4><ul><li>Sell Your Home</li><li>How it works</li><li>Stop foreclosure</li><li>Probate</li><li>Contact</li></ul></section>
  <section><h4>Get Social</h4><ul><li><span class="dot"></span>Fan Page</li><li><span class="dot"></span>Updates</li><li><span class="dot"></span>Circles</li><li><span class="dot"></span>Network</li></ul></section>
  <section><h4>Stay in Touch</h4><ul><li>2240 Harbor Row #12</li><li>Winter Park FL 32789</li><li>407-555-0148</li><li style="color:var(--red)">hello@quickdeedsale.com</li></ul></section>
</footer>
<div class="bottom-strip"><span>Copyright © 2015 - quickdeedsale.com All Rights Reserved</span><span>Privacy Policy · Terms &amp; Conditions</span></div>

</body>
</html>
```